Business Card Design Project

We are not a new company, but renamed to "Vantorin Kitchens" last year. We specialize in modern high-end cabinetry imports. We would like to communicate a sense of quality and cutting edge technology. Ideally the design would incorporate our logo colors, silver, red and preferably a black, matte background. Though we are open to suggestions.
Logo is attached.
Edit: I have attached rough drafts of the previous cards, this way you will have all necessary content that needs to go on the cards.
Updates
Project Deadline Extended
Reason: We have received a lot of great designs, but due to the sheer number we couldn't respond to all. We will extend the deadline for another 7 days to finalize and provide feedback to designers.
Thank you for your hard work!
Industry/Entity Type
Business
Look and feel
Each slider illustrates characteristics of the customer's brand and the style your logo design should communicate.

```html
<!DOCTYPE html>
<html lang="en">
<head>
<meta charset="UTF-8">
<title>Vantorin Kitchens — Business Card</title>
<link href="https://fonts.googleapis.com/css2?family=Exo+2:wght@300;400;600&display=swap" rel="stylesheet">
<style>
  :root {
    --backdrop: #3a302b;
    --card-black: #1c1c1d;
    --card-edge: #2a2a2b;
    --silver: #c9cacc;
    --silver-soft: #a9aaad;
    --accent-red: #d3202a;
    --rule: #8d8e91;
  }
  * { margin: 0; padding: 0; box-sizing: border-box; }
  html, body {
    width: 1200px;
    height: 716px;
    overflow: hidden;
    background: var(--backdrop);
    font-family: "Exo 2", sans-serif;
  }
  .canvas {
    position: relative;
    width: 1200px;
    height: 716px;
    display: flex;
    align-items: center;
    justify-content: center;
    gap: 44px;
  }
  .card {
    position: relative;
    width: 530px;
    height: 303px;
    background: var(--card-black);
    border: 1px solid var(--card-edge);
    box-shadow: 0 14px 30px rgba(0,0,0,0.45);
  }

  /* Front */
  .card--front {
    display: flex;
    align-items: center;
    justify-content: center;
  }
  .brand {
    display: flex;
    align-items: center;
    gap: 16px;
    color: var(--silver);
    font-weight: 600;
    font-size: 38px;
    letter-spacing: 1px;
    text-transform: uppercase;
  }
  .brand__square {
    width: 30px;
    height: 30px;
    background: var(--silver);
  }

  /* Back */
  .contact {
    position: absolute;
    left: 36px;
    top: 60px;
    color: var(--silver);
  }
  .contact__name {
    font-size: 19px;
    line-height: 23px;
    font-weight: 300;
    letter-spacing: 0.5px;
    text-transform: uppercase;
  }
  .contact__title {
    font-size: 10px;
    line-height: 13px;
    font-weight: 300;
    color: var(--silver-soft);
    margin-top: 1px;
  }
  .contact__lines {
    list-style: none;
    margin-top: 14px;
    font-size: 14px;
    font-weight: 300;
    line-height: 19px;
  }
  .contact__label {
    display: inline-block;
    width: 18px;
    color: var(--accent-red);
    font-size: 11px;
  }
  .contact__email {
    margin-top: 1px;
    font-size: 13px;
    line-height: 17px;
    font-weight: 300;
  }
  .card__rule {
    position: absolute;
    left: 36px;
    right: 36px;
    top: 212px;
    height: 1px;
    background: var(--rule);
  }
  .back-brand {
    position: absolute;
    right: 36px;
    top: 112px;
    display: flex;
    align-items: center;
    gap: 10px;
    color: var(--silver);
    font-weight: 600;
    font-size: 20px;
    text-transform: uppercase;
    letter-spacing: 0.5px;
  }
  .back-brand__square {
    width: 18px;
    height: 18px;
    background: var(--silver);
  }
  .address {
    position: absolute;
    right: 36px;
    top: 224px;
    text-align: left;
    font-style: normal;
    color: var(--silver);
    font-size: 14px;
    font-weight: 300;
    line-height: 19px;
  }
  .address__web {
    color: var(--accent-red);
    font-weight: 400;
    letter-spacing: 0.5px;
  }
</style>
</head>
<body>
<main class="canvas">
  <section class="card card--front" aria-label="Card front">
    <div class="brand">
      <span class="brand__square"></span>
      <span class="brand__name">Vantorin Kitchens</span>
    </div>
  </section>

  <section class="card card--back" aria-label="Card back">
    <div class="contact">
      <p class="contact__name">Marcus Delane</p>
      <p class="contact__title">Director</p>
      <ul class="contact__lines">
        <li><span class="contact__label">P</span>780.555.0142</li>
        <li><span class="contact__label">F</span>780.555.0178</li>
        <li><span class="contact__label">C</span>780.555.0193</li>
      </ul>
      <p class="contact__email">marcus@vantorinkitchens.ca</p>
    </div>

    <div class="back-brand">
      <span class="back-brand__square"></span>
      <span>Vantorin Kitchens</span>
    </div>

    <div class="card__rule"></div>

    <address class="address">
      2180 - 84 Ave.<br>
      Riverton, AB T4K 2M9<br>
      <span class="address__web">vantorinkitchens.ca</span>
    </address>
  </section>
</main>
</body>
</html>
```